House Cleaning Platform for Consumers and Cleaners

UPDATE: I've attached screenshots showing a purchase flow example, something all designers have missed in their designs. PLEASE check the URLs I've included in the brief for examples of a cleaning website. I've seen mostly landing pages and nothing else.

WHAT I'M LOOKING FOR:
I need the UI designed for a house cleaning web platform from 2 separate experiences: one from the consumer end to order a cleaner to come clean their house and one from a cleaner’s end that manages their orders and manages their schedule.

The UI will need to include photo uploading for before and after photos, a checkout/cart experience w/ tips, toggle options for adding and removing rooms/extras cleaning add-ons, customer+cleaner reviews (meaning the cleaner finished the job and they can rate and review the customer as well as the customer can rate and review the cleaner), order history for consumers, job history for cleaners, profile, settings, and landing pages for both.

PLEASE DO NOT USE THE COLOR BLUE AS THE PRIMARY COLOR. Use a light green (HEX #2fdf86) instead for primary theming color.

REFERENCES:
If you'd like a few websites I've enjoyed for references, checkout:
larkpolish.example, vomby.example, and brightfernhome.example.

For sake of branding, the company name is PlumNest. Currently do not have a logo as we have not decided on the name. Logo will come later.

Feel free to reach out to me if you have any questions!
Updates

Most designer submissions were a landing page and only a landing page. Very few designed the flows I requested and none designed a schedule management page. I even updated the Brief to more clearly outline the needs and references. Only about 2-3 of the designers actually did more than a landing page. Still don't believe I received 6 designers input that I had paid for.

Target Market(s)

FULL-TIME WORKING HOUSEHOLDS, SINGLE PROFESSIONALS, SINGLE PARENTS, ELDERLY & MOBILITY CHALLENGED, BUSY BODIES.

Industry/Entity Type

Cleaning, gig work.

Number of Pages Required

5+ page

Font styles to use
Other font styles liked:
• Jost or Lexend are great Google Font options I've used in the pitch deck and horribly done app mockups.

Colors
00AB8E
00BBA5
67D7C9
C6EFE9
E9F9F6
59FF00
82FF00
B8FF75
E3FFCB
F4FFEA
FFF300
FFF600
FEFA6F
FFFEC7
FFFEE8
FFC000
F8CF3A
FAE287
FDF2CF
FEFAEE

Requirements
Must have
• Landing page, consumer flow, cleaner schedule management, checkout flow, Rate & Review for consumer and/or cleaner, order history, profile.
Nice to have
• I'd like it to be simple in design and modern, but not so simple it's boring. Iconography can sometimes break that up, but I don't want it looking busy. It's a cleaning platform so the UI should look clean.

```html
<!DOCTYPE html>
<html lang="en">
<head>
<meta charset="utf-8">
<title>PlumNest – Book Your Services Now</title>
<link rel="stylesheet" href="https://fonts.googleapis.com/css2?family=Lexend:wght@300;400;500&family=Open+Sans:wght@600;700&display=swap">
<style>
  :root {
    --green: #2fdf86;
    --green-strong: #22d07e;
    --orange: #f7931e;
    --ink: #111111;
    --body: #4a4a4a;
    --muted: #b5b5b5;
    --line: #cfcfcf;
    --step-line: #dddddd;
    --icon-fill: #e9f9f6;
    --bg: #ffffff;
  }
  * { box-sizing: border-box; margin: 0; padding: 0; }
  html, body { width: 1200px; height: 972px; overflow: hidden; background: var(--bg); }
  body { font-family: "Lexend", sans-serif; color: var(--ink); position: relative; }
  .abs { position: absolute; }

  .brand { left: 102px; top: 18px; font-family: "Open Sans", sans-serif; font-weight: 700; font-size: 31px; color: var(--green); letter-spacing: -0.3px; }
  .nav { left: 438px; top: 27px; display: flex; gap: 19px; font-size: 11.5px; font-weight: 400; }
  .search { left: 731px; top: 22px; width: 218px; height: 25px; border: 1px solid #d9d9d9; border-radius: 13px; display: flex; align-items: center; padding-left: 8px; gap: 14px; font-size: 11.5px; }
  .login { left: 981px; top: 27px; font-size: 11.5px; }
  .signup { left: 1024px; top: 22px; width: 75px; height: 25px; border-radius: 13px; background: var(--green-strong); font-size: 10.5px; display: flex; align-items: center; justify-content: center; }

  .page-title { left: 0; width: 1200px; top: 126px; text-align: center; font-family: "Open Sans", sans-serif; font-weight: 700; font-size: 37px; }

  .stepper { left: 155px; top: 210px; }

  .field-icon { width: 62px; height: 62px; border: 1.5px solid var(--green); border-radius: 50%; display: flex; align-items: center; justify-content: center; }
  .field-icon span { width: 34px; height: 34px; border-radius: 8px; background: var(--icon-fill); display: block; }
  .field-title { font-family: "Open Sans", sans-serif; font-weight: 600; font-size: 20px; }
  .field-desc { font-size: 11.2px; line-height: 18px; font-weight: 300; color: var(--body); }
  .field-desc b { font-weight: 400; color: var(--ink); }
  .input { width: 469px; height: 38px; border: 1px solid var(--line); font-size: 11.2px; font-weight: 300; color: var(--muted); display: flex; align-items: center; justify-content: space-between; padding: 0 20px 0 18px; }

  .radio { top: 750px; display: flex; align-items: center; gap: 13px; font-size: 11.8px; }
  .dot { width: 13px; height: 13px; border-radius: 50%; border: 1px solid #c8c8c8; }
  .dot.on { border: 3.5px solid var(--green-strong); }

  .btn { top: 829px; width: 175px; height: 50px; border-radius: 25px; display: flex; align-items: center; justify-content: center; font-size: 16px; font-weight: 500; }
  .btn-back { left: 101px; border: 1px solid var(--line); }
  .btn-next { left: 307px; background: var(--green-strong); }
</style>
</head>
<body>
  <header>
    <div class="abs brand">PlumNest</div>
    <nav class="abs nav"><span>Home</span><span>Pricing</span><span>Services</span><span>Contact</span><span>Help</span></nav>
    <div class="abs search">
      <svg width="13" height="13" viewBox="0 0 14 14" fill="none" stroke="#222" stroke-width="1.2"><circle cx="6" cy="6" r="5"/><path d="M9.7 9.7 13 13"/></svg>
      <span>Search</span>
    </div>
    <div class="abs login">Login</div>
    <div class="abs signup">Sign Up</div>
  </header>

  <h1 class="abs page-title">Book Your Services Now</h1>

  <svg class="abs stepper" width="890" height="26" viewBox="0 0 890 26" aria-label="Step 1 of 8">
    <line x1="24" y1="13" x2="866" y2="13" stroke="var(--step-line)" stroke-width="2"/>
    <g fill="#fff" stroke-width="1.6">
      <circle cx="12" cy="13" r="11.5" stroke="var(--orange)"/>
      <circle cx="136" cy="13" r="11.5" stroke="#d0d0d0"/>
      <circle cx="259" cy="13" r="11.5" stroke="#d0d0d0"/>
      <circle cx="383" cy="13" r="11.5" stroke="#d0d0d0"/>
      <circle cx="507" cy="13" r="11.5" stroke="#d0d0d0"/>
      <circle cx="631" cy="13" r="11.5" stroke="#d0d0d0"/>
      <circle cx="754" cy="13" r="11.5" stroke="#d0d0d0"/>
      <circle cx="878" cy="13" r="11.5" stroke="#d0d0d0"/>
    </g>
  </svg>

  <section>
    <div class="abs field-icon" style="left:101px;top:297px"><span role="img" aria-label="Envelope with zip pin icon"></span></div>
    <h2 class="abs field-title" style="left:177px;top:298px">Enter Property Zip Code</h2>
    <p class="abs field-desc" style="left:176px;top:339px;width:380px">Enter your Zip Code. The zip code helps us to pull accurate quote and pricing details.</p>
    <div class="abs input" style="left:101px;top:394px">Zip Code</div>

    <div class="abs field-icon" style="left:630px;top:297px"><span role="img" aria-label="House icon"></span></div>
    <h2 class="abs field-title" style="left:705px;top:298px">Total Square Feet At Home</h2>
    <p class="abs field-desc" style="left:705px;top:339px;width:400px">Enter your total square feet of your home. This number will be verified by our system.</p>
    <div class="abs input" style="left:630px;top:394px">Zip Code</div>

    <div class="abs field-icon" style="left:101px;top:482px"><span role="img" aria-label="Bed icon"></span></div>
    <h2 class="abs field-title" style="left:177px;top:483px">How Many Bedrooms?</h2>
    <p class="abs field-desc" style="left:176px;top:524px;width:390px">Enter total number of bedrooms in the home. You can Exclude number of Bedrooms at a later step.</p>
    <div class="abs input" style="left:101px;top:579px">Select Bedrooms
      <svg width="11" height="6" viewBox="0 0 11 6"><path d="M0 0h11L5.5 6z" fill="#111"/></svg></div>

    <div class="abs field-icon" style="left:629px;top:482px"><span role="img" aria-label="Bathtub icon"></span></div>
    <h2 class="abs field-title" style="left:704px;top:483px">How Many Bathrooms?</h2>
    <p class="abs field-desc" style="left:704px;top:524px;width:400px">Enter total number of bathrooms in the home. <b>Round half baths up</b> (this will not affect price). You can Exclude Bedrooms at a later step.</p>
    <div class="abs input" style="left:629px;top:579px">Select Bathhrooms
      <svg width="11" height="6" viewBox="0 0 11 6"><path d="M0 0h11L5.5 6z" fill="#111"/></svg></div>

    <div class="abs field-icon" style="left:101px;top:667px"><span role="img" aria-label="Pets icon"></span></div>
    <h2 class="abs field-title" style="left:176px;top:668px">Any Pets At Home?</h2>
    <p class="abs field-desc" style="left:176px;top:709px;width:600px">This include any cats or dogs that live in or spend time in the same home. Select any one.</p>

    <div class="abs radio" style="left:101px"><span class="dot on"></span>No pets in the home</div>
    <div class="abs radio" style="left:299px"><span class="dot"></span>Dog(s)</div>
    <div class="abs radio" style="left:421px"><span class="dot"></span>Cats(s)</div>
    <div class="abs radio" style="left:545px"><span class="dot"></span>Dog(s) and Cats(s)</div>
  </section>

  <div class="abs btn btn-back">Back</div>
  <div class="abs btn btn-next">Save &amp; Next</div>
</body>
</html>
```